Creative, fresh business card design for Ripplecraft Facades

We need a fresh, creative business card design for Ripplecraft Facades. We are the manufacturer of Ripplecraft Facades in Australia. Wall panels are 2400 x 1200mm panels made from MDF and feature 3D patterns on the face of the panel. The colours to be used are green, silver/grey and white RGB
Red 187
Green 207
Blue 65.

An idea is to possibly use a watermark of one of our designs as a background (like on the "Grids" design on the left hand side of page 2 of our brochure).

Target Market(s)

Interior designers, architects, builders and home renovators

Industry/Entity Type

Business

Contact Information for Business Card

Details to go on the card are:
Our logo (attached),
Slogan: "Decorative panels for interiors and exteriors",
Contact name,
Position,
Mobile phone number,
Business address,
Business phone,
Business fax,
Website and
Email address.

I have attached a few images of our panels and our brochure for reference.

The colours of the business card should feature our logo colours which are: RGB
Red 187
Green 207
Blue 65

Requirements
Must have
• Very modern fonts and design. Some of the designs shown especially the "Prisms" design which is a popular design.
Nice to have
• Creative but simple design. Very contemporary.
Should not have
• Anything ornate or old fashioned.

```html
<!DOCTYPE html>
<html lang="en">
<head>
<meta charset="utf-8">
<title>Ripplecraft Facades – Business Card</title>
<link rel="stylesheet" href="https://fonts.googleapis.com/css2?family=Source+Sans+3:wght@400;600;700&display=swap">
<style>
  :root {
    --brand-green: rgb(187, 207, 65);
    --panel-green: #c2d82e;
    --silver: #8e8f93;
    --ink: #4a4a4c;
    --white: #ffffff;
    --backdrop: #5c4b3e;
    --text-font: "Source Sans 3", Arial, sans-serif;
  }
  * { box-sizing: border-box; margin: 0; padding: 0; }
  html, body {
    width: 1200px; height: 987px; overflow: hidden;
    background: var(--backdrop);
    font-family: var(--text-font);
  }
  .stage { position: relative; width: 1200px; height: 987px; }

  .card {
    position: absolute; left: 293px; width: 615px; height: 351px;
    box-shadow: 0 3px 6px rgba(0,0,0,0.35);
  }
  .card--front { top: 130px; background: var(--white); }
  .card--back  { top: 505px; background: var(--panel-green); }

  /* Front */
  .holder { position: absolute; top: 48px; left: 0; width: 615px; text-align: center; }
  .holder__name { color: var(--brand-green); font-weight: 700; font-size: 22px; letter-spacing: 0.3px; }
  .holder__role { color: var(--silver); font-size: 16px; margin-top: 1px; }

  .brand { position: absolute; display: flex; align-items: center; gap: 10px; }
  .brand__square { width: 30px; height: 30px; flex: none; }
  .brand__name { font-weight: 600; white-space: nowrap; }
  .card--front .brand { left: 48px; top: 178px; }
  .card--front .brand__square { background: var(--brand-green); }
  .card--front .brand__name { color: var(--brand-green); font-size: 23px; }
  .slogan { position: absolute; font-size: 12.5px; letter-spacing: 2px; line-height: 1.2; text-align: center; }
  .card--front .slogan { left: 30px; width: 245px; top: 226px; color: var(--silver); }

  .divider { position: absolute; left: 303px; top: 125px; width: 1px; height: 181px; background: #d3d3d3; }

  .address { position: absolute; left: 333px; top: 136px; color: var(--ink); font-size: 15.5px; line-height: 22px; }
  .contacts { position: absolute; left: 333px; top: 198px; list-style: none; }
  .contacts li { display: flex; align-items: center; height: 23.5px; color: var(--ink); font-size: 15.5px; }
  .contacts svg { width: 16px; height: 16px; margin-right: 10px; fill: var(--brand-green); flex: none; }

  .edge-band { position: absolute; bottom: 0; height: 9px; }
  .edge-band--green { left: 0; width: 481px; background: var(--brand-green); }
  .edge-band--silver { left: 483px; right: 0; background: var(--silver); }

  /* Back */
  .card--back .brand { left: 0; width: 615px; justify-content: center; top: 118px; }
  .card--back .brand__square { background: var(--white); width: 36px; height: 36px; }
  .card--back .brand__name { color: var(--white); font-size: 32px; }
  .card--back .slogan { left: 0; width: 615px; top: 232px; color: var(--white); font-size: 14px; letter-spacing: 2.6px; }
  .website { position: absolute; left: 0; width: 615px; top: 292px; text-align: center; color: var(--white); font-size: 15px; letter-spacing: 3px; }
</style>
</head>
<body>
<main class="stage">

  <section class="card card--front" aria-label="Business card front">
    <div class="holder">
      <p class="holder__name">LIAM HARTLEY</p>
      <p class="holder__role">CEO&amp;Founder</p>
    </div>

    <div class="brand">
      <span class="brand__square"></span>
      <span class="brand__name">Ripplecraft Facades</span>
    </div>
    <p class="slogan">decorative panels for<br>interiors &amp; landscapes</p>

    <span class="divider"></span>

    <address class="address" style="font-style:normal">
      42 Wattle Street<br>Geelong, Victoria 3220
    </address>

    <ul class="contacts">
      <li>
        <svg viewBox="0 0 16 16" aria-hidden="true"><path d="M3.6 1.2l2.3 2.4-1.3 2c.9 1.9 2.4 3.4 4.3 4.4l2-1.3 2.4 2.3-1.5 2.6C6.9 13.3 2.7 9.1 1 4.2z"/></svg>
        (555) 318-2746
      </li>
      <li>
        <svg viewBox="0 0 16 16" aria-hidden="true"><path d="M4 1h8v4H4zM1 6h14v6h-2V9H3v3H1zM4 10h8v5H4z"/></svg>
        (555) 318-2790
      </li>
      <li>
        <svg viewBox="0 0 16 16" aria-hidden="true"><path d="M1 3h14v1.2L8 8.6 1 4.2zM1 5.8l7 4.4 7-4.4V13H1z"/></svg>
        lhartley@ripplecraftfacades.com
      </li>
      <li>
        <svg viewBox="0 0 16 16" aria-hidden="true"><path d="M8 1a7 7 0 1 0 0 14A7 7 0 0 0 8 1zm-1 2.2c.6.6.2 1.5-.6 1.9-.9.4-1.3 1.2-.7 2 .6.8 1.8.6 2.3 1.5.4.8-.2 1.9-.9 2.8-.5.6-.4 1.4-.1 2A5.6 5.6 0 0 1 7 3.2zm3.2.5A5.6 5.6 0 0 1 13.3 10c-.7-.2-1.2-.9-1.4-1.7-.2-.9-1.2-1.1-1.5-1.9-.3-.8.3-1.4.2-2.2z"/></svg>
        www.ripplecraftfacades.com
      </li>
    </ul>

    <span class="edge-band edge-band--green"></span>
    <span class="edge-band edge-band--silver"></span>
  </section>

  <section class="card card--back" aria-label="Business card back">
    <div class="brand">
      <span class="brand__square"></span>
      <span class="brand__name">Ripplecraft Facades</span>
    </div>
    <p class="slogan">decorative panels for<br>interiors &amp; landscapes</p>
    <p class="website">www.ripplecraftfacades.com</p>
  </section>

</main>
</body>
</html>
```